BrivoTerna. Lantern of the Steady Harvest. Business card

Professional business card for BrivoTerna (Lantern of the Steady Harvest)
My rationale: Strategy-> Execution-> Results-> Value that lead to the BrivoTerna name: We put the Lantern of the Steady Harvest.
We deliver value to our customers helping them at defining a good strategy (cyan arrow). 90% of well formulated strategies fail due to poor execution so we also consider strategical execution very important (green arrow). Due to the execution we obtain the results (blue arrow). Finally, the results provide feedback to redefine strategy, and the new strategy has to be executed and new results obtained providing new feedback and on and on. It's like a wheel that finally, must create corporate value: value for shareholders, staholders, employees, providers...-

Target Market(s)

CEOs and steering comitees , invewrnent funds

Industry/Entity Type

Business Consultant

Contact Information for Business Card

Teodoro Vinsquel
CEO & Founder
teodoro.vinsquel@brivoterna-example.com
Mobile: +34 655.803.912
www.brivoterna-example.com

Colors

Designer to choose colors to be used in the design.

Requirements
Nice to have
• Nice to hace the words: Strategy, execution, results
• Nice to vave the claim: Lantern of the Steady Harvest
• The three colors should be shown:
• cyan for STRATEGY
• green for EXECUTION
• blue for RESULTS
Should not have
• Complete black background

```html
<!DOCTYPE html>
<html lang="en">
<head>
<meta charset="utf-8">
<title>BrivoTerna — Stationery</title>
<link href="https://fonts.googleapis.com/css2?family=Arimo:wght@400;700&family=Open+Sans:wght@700&family=Montserrat:wght@400&display=swap" rel="stylesheet">
<style>
  :root {
    --navy: #21367f;
    --cyan: #22a0d3;
    --green: #86b73a;
    --paper: #e6e6e6;
    --ink: #808080;
    --dark-ink: #1c1c1c;
    --stage: #cdcdcd;
    --white: #f2f2f2;
  }
  * { margin: 0; padding: 0; box-sizing: border-box; }
  html, body { width: 1200px; height: 891px; overflow: hidden; }
  body { background: var(--stage); position: relative; font-family: "Arimo", sans-serif; }

  .letterhead { position: absolute; left: 52px; top: 74px; width: 579px; height: 742px; background: var(--paper); overflow: hidden; }
  .footer-band { position: absolute; left: 0; width: 100%; background: var(--navy); }
  .stripe { position: absolute; left: 0; width: 100%; }
  .stripe-green { background: var(--green); }
  .stripe-cyan { background: var(--cyan); }

  .letterhead .stripe-green { top: 660px; height: 6px; }
  .letterhead .stripe-cyan { top: 670px; height: 4px; }
  .letterhead .footer-band { top: 678px; bottom: 0; }

  .brand-name { font-family: "Open Sans", sans-serif; font-weight: 700; color: var(--navy); letter-spacing: -0.5px; white-space: nowrap; }
  .letterhead .brand-name { position: absolute; left: 0; width: 100%; text-align: center; top: 82px; font-size: 34px; }
  .field { position: absolute; font-size: 9px; color: var(--ink); line-height: 12px; }
  .field b { display: block; color: var(--dark-ink); font-weight: 700; }
  .subject { left: 176px; top: 180px; }
  .date { left: 481px; top: 178px; }
  .salutation { position: absolute; left: 176px; top: 254px; font-size: 11.5px; font-weight: 700; color: var(--ink); }
  .letter-body { position: absolute; left: 176px; top: 280px; width: 354px; }
  .letter-body p { font-size: 9.2px; line-height: 12.35px; color: var(--ink); text-align: justify; margin-bottom: 12.3px; }
  .side-note { position: absolute; left: 20px; top: 313px; width: 110px; text-align: right; font-size: 8.8px; line-height: 12.2px; color: var(--ink); }
  .side-note span { color: var(--dark-ink); }
  .side-note .gap { display: block; height: 6px; }
  .signature { position: absolute; left: 176px; top: 546px; font-size: 11.5px; font-weight: 700; color: var(--ink); line-height: 15px; }
  .contact { position: absolute; font-family: "Montserrat", sans-serif; color: var(--white); text-align: right; }
  .contact li { list-style: none; display: flex; justify-content: flex-end; align-items: center; gap: 8px; }
  .contact svg { width: 10px; height: 10px; }
  .letterhead .contact { right: 32px; top: 694px; font-size: 9.4px; line-height: 13.4px; }

  .card { position: absolute; left: 681px; width: 452px; height: 262px; border-radius: 34px; overflow: hidden; }
  .card-front { top: 156px; background: var(--paper); }
  .card-front .brand-name { position: absolute; left: 21px; top: 94px; font-size: 36px; }
  .card-front .stripe-green { top: 168px; height: 8px; }
  .card-front .stripe-cyan { top: 180px; height: 4px; }
  .card-front .footer-band { top: 188px; bottom: 0; }
  .holder { position: absolute; left: 21px; top: 212px; font-family: "Montserrat", sans-serif; color: var(--white); }
  .holder .name { font-size: 14px; line-height: 17px; }
  .holder .role { font-size: 10.5px; line-height: 14px; }
  .card-front .contact { right: 20px; top: 200px; font-size: 10.4px; line-height: 15px; }

  .card-back { top: 470px; background: var(--navy); }
  .card-back .brand-name { position: absolute; left: 0; width: 100%; text-align: center; top: 118px; font-size: 38px; color: var(--white); }
  .tagline { position: absolute; left: 0; width: 100%; text-align: center; top: 170px; font-family: "Montserrat", sans-serif; font-size: 11.5px; color: var(--white); }
  .process { position: absolute; left: 0; top: 214px; width: 100%; height: 26px; background: var(--white); }
  .process svg { position: absolute; left: 0; top: 0; }
  .step { position: absolute; top: 5px; font-family: "Arimo", sans-serif; font-size: 14px; letter-spacing: 0.3px; transform: translateX(-50%); }
  .step-strategy { left: 75px; color: var(--cyan); }
  .step-execution { left: 220px; color: var(--green); }
  .step-results { left: 372px; color: var(--navy); }
</style>
</head>
<body>

<section class="letterhead">
  <div class="stripe stripe-green"></div>
  <div class="stripe stripe-cyan"></div>
  <div class="footer-band"></div>

  <div class="brand-name">BrivoTerna</div>

  <div class="field subject"><b>SUBJECT :</b>Lorem Ipsum is simply dummy</div>
  <div class="field date"><b>DATE :</b>15-09-2017</div>

  <div class="salutation">Dear Person,</div>

  <div class="side-note">
    <span>Lorem Ipsum is</span><br>simply dummy text<br>of the printing
    <i class="gap"></i>
    <span>Lorem Ipsum is</span><br>simply dummy text
  </div>

  <div class="letter-body">
    <p>Lorem Ipsum is simply dummy text of the printing and typesetting industry. Lorem Ipsum has been the industry's standard dummy text ever since the 1500s, when an unknown printer took a galley of type and scrambled it to make a type specimen book. It has survived not only five centuries, but also the leap into electronic typesetting, remaining essentially unchanged. It was popularised in the 1960s with the release of Typeleaf sheets containing Lorem Ipsum passages, and more recently with desktop publishing software like Folio Setwright including versions of Lorem Ipsum.</p>
    <p>Lorem Ipsum is simply dummy text of the printing and typesetting industry. Lorem Ipsum has been the industry's standard dummy text ever since the 1500s, when an unknown printer took a galley of type and scrambled it to make a type specimen book. It has survived not only five centuries, but also the leap into electronic typesetting, remaining essentially unchanged. It was popularised in the 1960s with the release of</p>
    <p>Typeleaf sheets containing Lorem Ipsum passages, and more recently with desktop publishing software like Folio Setwright including versions of Lorem Ipsum.lease of Typeleaf sheets containing Lorem Ipsum passages, and more recently with desktop publishing software like Folio Setwright including versions of Lorem Ipsum.</p>
  </div>

  <div class="signature">Marlo Quentiv<br>Managing Director</div>

  <ul class="contact">
    <li>+34 655.803.912 <svg viewBox="0 0 10 10"><circle cx="5" cy="5" r="4.5" fill="#f2f2f2"/><path d="M2.6,6.4h4.8v-1.3l-1-1.2h-2.8l-1,1.2z" fill="#21367f"/></svg></li>
    <li>teodoro.vinsquel@brivoterna-example.com <svg viewBox="0 0 10 10"><circle cx="5" cy="5" r="4.5" fill="#f2f2f2"/><rect x="2.6" y="3.4" width="4.8" height="3.2" fill="none" stroke="#21367f" stroke-width=".8"/><path d="M2.6,3.4l2.4,2l2.4,-2" fill="none" stroke="#21367f" stroke-width=".8"/></svg></li>
    <li>www.brivoterna-example.com <svg viewBox="0 0 10 10"><circle cx="5" cy="5" r="4.5" fill="#f2f2f2"/><circle cx="5" cy="5" r="2.6" fill="none" stroke="#21367f" stroke-width=".8"/><path d="M2.4,5h5.2M5,2.4v5.2" stroke="#21367f" stroke-width=".6"/></svg></li>
  </ul>
</section>

<section class="card card-front">
  <div class="stripe stripe-green"></div>
  <div class="stripe stripe-cyan"></div>
  <div class="footer-band"></div>

  <div class="brand-name">BrivoTerna</div>

  <div class="holder">
    <div class="name">Teodoro Vinsquel</div>
    <div class="role">CEO &amp; Founder</div>
  </div>

  <ul class="contact">
    <li>+34 655.803.912 <svg viewBox="0 0 10 10"><circle cx="5" cy="5" r="4.5" fill="#f2f2f2"/><path d="M2.6,6.4h4.8v-1.3l-1-1.2h-2.8l-1,1.2z" fill="#21367f"/></svg></li>
    <li>teodoro.vinsquel@brivoterna-example.com <svg viewBox="0 0 10 10"><circle cx="5" cy="5" r="4.5" fill="#f2f2f2"/><rect x="2.6" y="3.4" width="4.8" height="3.2" fill="none" stroke="#21367f" stroke-width=".8"/><path d="M2.6,3.4l2.4,2l2.4,-2" fill="none" stroke="#21367f" stroke-width=".8"/></svg></li>
    <li>www.brivoterna-example.com <svg viewBox="0 0 10 10"><circle cx="5" cy="5" r="4.5" fill="#f2f2f2"/><circle cx="5" cy="5" r="2.6" fill="none" stroke="#21367f" stroke-width=".8"/><path d="M2.4,5h5.2M5,2.4v5.2" stroke="#21367f" stroke-width=".6"/></svg></li>
  </ul>
</section>

<section class="card card-back">
  <div class="brand-name">BrivoTerna</div>
  <div class="tagline">Lantern of the Steady Harvest</div>
  <div class="process">
    <svg width="452" height="26" viewBox="0 0 452 26" aria-hidden="true">
      <path d="M136,0 L151,13 L136,26" fill="none" stroke="#21367f" stroke-width="1.4"/>
      <path d="M289,0 L304,13 L289,26" fill="none" stroke="#21367f" stroke-width="1.4"/>
    </svg>
    <span class="step step-strategy">STRATEGY</span>
    <span class="step step-execution">EXECUTION</span>
    <span class="step step-results">RESULTS</span>
  </div>
</section>

</body>
</html>
```